Kestrel Home Business Card Design

We need a business card for a Building company based in Queensland, Australia. Our colours are orange black and we do base all our homes design names and other aspect of our business on astrology. We want the consumer to perceive the company as professional and to attract investors to our company.We have over 20 years in the building industry.We pride ourselves on our innovation of designs and making the building process for anyone from families to investor a smooth and simple experience.
Business
Amelia Prichard0411752116PO Box 454, Mudgeerbaameliaprichard@zodiachomes.com

```html
<!DOCTYPE html>
<html lang="en">
<head>
<meta charset="utf-8">
<title>Kestrel Homes Business Card</title>
<link rel="stylesheet" href="https://fonts.googleapis.com/css2?family=Poppins:wght@700&family=Open+Sans:wght@400;700&display=swap">
<style>
  :root {
    --backdrop: #e4e4e4;
    --orange: #e8791a;
    --orange-light: #ee8a30;
    --ink: #1a1a1a;
    --paper: #ffffff;
  }
  * { margin: 0; padding: 0; box-sizing: border-box; }
  html, body { width: 1200px; height: 852px; overflow: hidden; }
  body {
    background: var(--backdrop);
    position: relative;
    font-family: "Open Sans", Arial, sans-serif;
    color: var(--ink);
  }
  .card {
    position: absolute;
    width: 520px;
    height: 300px;
    border-radius: 26px;
    overflow: hidden;
    background: var(--orange);
  }
  .card--front { left: 70px; top: 120px; }
  .card--back { left: 610px; top: 430px; }

  .front__halo {
    position: absolute;
    right: -60px;
    top: -70px;
    width: 300px;
    height: 300px;
    border-radius: 50%;
    background: var(--orange-light);
    opacity: 0.45;
  }
  .front__brand {
    position: absolute;
    left: 0; right: 0; top: 62px;
    display: flex;
    flex-direction: column;
    align-items: center;
    gap: 18px;
  }
  .brand__dot {
    width: 84px;
    height: 84px;
    border-radius: 50%;
    background: var(--ink);
  }
  .brand__name {
    font-family: "Poppins", Arial, sans-serif;
    font-weight: 700;
    font-size: 40px;
    line-height: 1;
    color: var(--ink);
  }

  .back__shape { position: absolute; inset: 0; }
  .back__brand {
    position: absolute;
    right: 18px;
    top: 40px;
    width: 140px;
    display: flex;
    flex-direction: column;
    align-items: center;
    gap: 12px;
  }
  .back__brand .brand__dot { width: 62px; height: 62px; }
  .back__brand .brand__name { font-size: 26px; text-align: center; line-height: 1.05; }

  .contact {
    position: absolute;
    left: 44px;
    top: 150px;
  }
  .contact__name {
    font-family: "Open Sans", Arial, sans-serif;
    font-weight: 700;
    font-size: 18px;
    color: var(--ink);
  }
  .contact__role { font-size: 12px; margin-top: 2px; }
  .contact__list { list-style: none; margin-top: 22px; }
  .contact__item {
    display: flex;
    align-items: center;
    gap: 10px;
    font-size: 12.5px;
    line-height: 20px;
  }
  .contact__icon { width: 12px; height: 12px; flex: none; }
</style>
</head>
<body>

<section class="card card--front" aria-label="Business card front">
  <div class="front__halo"></div>
  <div class="front__brand">
    <div class="brand__dot"></div>
    <div class="brand__name">Kestrel Homes</div>
  </div>
</section>

<section class="card card--back" aria-label="Business card back">
  <svg class="back__shape" viewBox="0 0 520 300" width="520" height="300" aria-hidden="true">
    <path d="M268,0 C300,50 312,110 340,165 C368,220 400,265 408,300 L520,300 L520,0 Z" fill="var(--ink)"/>
    <path d="M280,0 C312,50 324,108 352,164 C380,218 414,262 420,300 L520,300 L520,0 Z" fill="var(--paper)"/>
  </svg>

  <div class="back__brand">
    <div class="brand__dot"></div>
    <div class="brand__name">Kestrel<br>Homes</div>
  </div>

  <div class="contact">
    <div class="contact__name">Harriet Colvane</div>
    <div class="contact__role">Owner / Proprietor</div>
    <ul class="contact__list">
      <li class="contact__item">
        <svg class="contact__icon" viewBox="0 0 12 12" aria-hidden="true"><rect x="2.5" y="0.5" width="7" height="11" rx="1.2" fill="none" stroke="var(--ink)" stroke-width="1.2"/><circle cx="6" cy="9.5" r="0.8" fill="var(--ink)"/></svg>
        0487309625
      </li>
      <li class="contact__item">
        <svg class="contact__icon" viewBox="0 0 12 12" aria-hidden="true"><path d="M6,11.5 C3,8 1.8,6 1.8,4.3 A4.2,4.2 0 0 1 10.2,4.3 C10.2,6 9,8 6,11.5 Z" fill="var(--ink)"/><circle cx="6" cy="4.3" r="1.5" fill="var(--orange)"/></svg>
        PO Box 872, Tallowbrook
      </li>
      <li class="contact__item">
        <svg class="contact__icon" viewBox="0 0 12 12" aria-hidden="true"><rect x="0.5" y="2" width="11" height="8" fill="var(--ink)"/><path d="M0.8,2.4 L6,6.6 L11.2,2.4" fill="none" stroke="var(--orange)" stroke-width="1"/></svg>
        harrietcolvane@kestrelhomes.example
      </li>
    </ul>
  </div>
</section>

</body>
</html>
```